Electric mountain bike tours nz

We are an Electric Mountain bike tour company in New Zealand. We will be offering bike rental and guided tours around the Nelson region in New Zealand. I want our website to represent both Mountain biking and New Zealand with the colours layout and features. We want tabs for the following:
-1 about us
-2 what we offer
-3 bookings/contact
Under the about us tab will be who we are as a a company. I want the ability to add videos to each of these tabs as we move foward with videos of the tracks we will be riding. I want the website to be editable so I can add and remove videos/photos myself. Also "our bikes" will be under this tab.
Under the what we offer tab will be
-1 bike rental and pricing
-2 guided tours and pricing
-3 recommended package deals.
I want to able to put the tracks under the guided tours tab and select beginner/ intermediate/advanced and have the tracks in each of the following to match the rider level. Also to be able to have a small video of the track would be great in this section.
Bookings and contact tab
(Further information for this tab to be updated soon)
Coded - Design and coding required
1 page
- Silver ferns, kiwi, mountains

```html
<!DOCTYPE html>
<html lang="en">
<head>
<meta charset="utf-8">
<title>Ridgevolt – Electric Mountain Bike Tours</title>
<link href="https://fonts.googleapis.com/css2?family=Lato:ital,wght@0,400;0,700;0,900;1,400&display=swap" rel="stylesheet">
<style>
:root{
  --orange:#f7931e;
  --ink:#1a1a1a;
  --body:#444;
  --white:#fff;
  --pink:#e5127d;
  --green:#5aab2a;
  --blue:#1f63b6;
}
*{margin:0;padding:0;box-sizing:border-box}
html,body{width:1200px;height:3974px;overflow:hidden}
body{font-family:'Lato',sans-serif;color:var(--body);background:var(--white);position:relative}
a{text-decoration:none}
.section{position:absolute;left:0;width:1200px}
.ridge{position:absolute;left:0;bottom:-1px;width:1200px;height:90px;display:block}
.btn{display:block;background:var(--orange);color:var(--white);font-weight:700;font-size:15px;text-transform:uppercase;text-align:center;letter-spacing:.3px}
.title{font-weight:900;font-size:36px;text-align:center;color:var(--ink);text-transform:uppercase;letter-spacing:.5px}
.lead{font-size:14.5px;line-height:28px;text-align:center}

/* hero */
.hero{top:0;height:728px;background:linear-gradient(160deg,#3c4a55 0%,#6d7b86 35%,#2d3338 70%,#1a1d20 100%)}
.hero-photo{position:absolute;inset:0}
.nav{position:absolute;top:60px;left:0;width:1200px;height:54px}
.nav-link{position:absolute;top:19px;color:var(--white);font-size:14px;font-weight:700;text-transform:uppercase}
.nav-book{position:absolute;top:0;left:1006px;width:122px;height:54px;line-height:54px}
.brand{position:absolute;display:flex;align-items:center;justify-content:center;gap:8px;color:var(--white);font-weight:900;font-size:26px;letter-spacing:1px;width:200px}
.nav .brand{left:500px;top:12px}
.brand i{width:14px;height:14px;border-radius:50%;background:var(--white);display:block}
.hero-title{position:absolute;left:77px;top:288px;font-weight:900;font-size:41px;line-height:48px;color:var(--white);text-transform:uppercase}
.hero-sub{position:absolute;left:77px;top:392px;font-size:25px;font-weight:700;color:var(--white)}
.hero-cta{position:absolute;left:77px;top:448px;width:177px;height:50px;line-height:50px}
.dots{position:absolute;left:77px;top:554px;display:flex;gap:8px}
.dots span{width:13px;height:13px;border-radius:50%;border:2px solid var(--white)}
.dots span.on{background:var(--orange);border-color:var(--orange)}

/* about */
.about{top:728px;height:427px}
.about .title{margin-top:67px}
.about .lead{width:920px;margin:22px auto 0}
.about .btn{position:absolute;left:511px;top:310px;width:178px;height:50px;line-height:50px}

/* offer */
.offer{top:1155px;height:700px;background:linear-gradient(180deg,#141719 0%,#25303a 45%,#1d2a22 100%)}
.offer .title{color:var(--white);margin-top:56px}
.offer .lead{color:#e8e8e8;width:920px;margin:12px auto 0}
.offer-card{position:absolute;top:204px;width:510px}
.offer-card .photo{width:510px;height:236px;border:4px solid #8b8b8b}
.offer-card h3{margin-top:34px;text-align:center;color:var(--white);font-weight:900;font-size:25px;text-transform:uppercase}
.offer-card p{text-align:center;color:#e8e8e8;font-size:14px;line-height:23px;margin-top:4px}

/* track */
.track{top:1855px;height:529px}
.track .title{margin-top:54px}
.track .lead{margin-top:10px}
.video{position:absolute;left:342px;top:177px;width:516px;height:296px;background:linear-gradient(180deg,#8fa7c2 0%,#b6c4cf 40%,#6f7a4a 65%,#4b5630 100%)}
.play{position:absolute;left:228px;top:118px;width:60px;height:60px}
.fern{position:absolute;left:0;top:278px;width:330px;height:240px;background:radial-gradient(ellipse 60% 55% at 45% 55%,#9a9a9a 0%,#c4c4c4 55%,rgba(255,255,255,0) 100%)}
.kiwi{position:absolute;left:922px;top:331px;width:204px;height:182px;background:radial-gradient(ellipse 55% 50% at 55% 55%,#5a4a38 0%,#8c7a66 55%,rgba(255,255,255,0) 100%)}

/* pricing */
.pricing{top:2384px;height:796px;background:linear-gradient(180deg,#2b3137 0%,#3e4a55 40%,#1d2227 100%)}
.pricing .title{color:var(--white);margin-top:62px}
.pricing .lead{color:#e8e8e8;width:920px;margin:10px auto 0}
.plan{position:absolute;top:215px;width:329px;height:453px;background:var(--white);text-align:center}
.badge{position:absolute;left:22px;top:28px;width:104px;height:104px;border-radius:50%;color:var(--white);font-weight:900;font-size:30px;line-height:28px;padding-top:26px}
.badge sup{font-size:14px;vertical-align:top}
.badge small{display:block;font-size:20px}
.bike{position:absolute;left:132px;top:34px;width:180px;height:98px;background:linear-gradient(180deg,#e9e9e9,#c9c9c9);border-radius:6px}
.plan h3{position:absolute;left:0;top:172px;width:100%;font-weight:900;font-size:29px;text-transform:uppercase}
.plan ul{position:absolute;left:0;top:224px;width:100%;list-style:none;font-size:14.5px;color:var(--body)}
.plan li{height:34px;line-height:34px}
.plan li::before{content:"";display:inline-block;width:9px;height:5px;border-left:2.5px solid var(--ink);border-bottom:2.5px solid var(--ink);transform:rotate(-45deg);margin-right:14px;vertical-align:4px}
.plan .btn{position:absolute;left:75px;top:377px;width:179px;height:50px;line-height:50px}
.basic .badge{background:var(--pink)} .basic h3{color:var(--pink)}
.standard .badge{background:var(--green)} .standard h3{color:var(--green)}
.premium .badge{background:var(--blue)} .premium h3{color:var(--blue)}

/* testimonials */
.testimonials{top:3180px;height:484px}
.testimonials .title{margin-top:56px}
.avatar{position:absolute;left:527px;top:131px;width:146px;height:146px;border-radius:50%;background:linear-gradient(180deg,#5d8fb8,#2f5f8a)}
.arrow{position:absolute;top:195px;width:18px;height:18px;border-left:4px solid #444;border-bottom:4px solid #444}
.arrow.prev{left:482px;transform:rotate(45deg)}
.arrow.next{left:700px;transform:rotate(-135deg)}
.quote{position:absolute;left:77px;top:304px;width:1046px;font-style:italic;font-size:14.5px;line-height:26px;text-align:center;color:var(--body)}
.cite{position:absolute;left:0;top:400px;width:1200px;text-align:center;color:var(--orange);font-weight:700;font-size:14px;text-transform:uppercase}

/* footer */
.footer{top:3664px;height:310px;background:linear-gradient(180deg,#1a1d20,#2a2f33)}
.footer .brand{left:94px;top:100px}
.copy{position:absolute;left:60px;top:186px;width:268px;text-align:center;font-size:12.5px;line-height:18px;color:#ddd}
.social{position:absolute;left:95px;top:234px;display:flex;gap:14px}
.social span{width:20px;height:20px;border-radius:50%;background:var(--white)}
.fcol{position:absolute;top:42px;color:var(--white)}
.fcol h4{font-size:15px;font-weight:900;text-transform:uppercase;margin-bottom:14px}
.fcol li{list-style:none;font-size:12.5px;font-weight:700;line-height:29px}
.fcol.contact li{line-height:19px;margin-bottom:12px;display:flex;gap:10px}
.fcol.contact svg{flex:none;margin-top:3px}
.email{position:absolute;left:885px;top:76px;width:241px;height:40px;background:var(--white);font-size:12.5px;color:#555;line-height:40px;padding-left:48px}
.email svg{position:absolute;left:14px;top:14px}
.signup{position:absolute;left:1036px;top:127px;width:90px;height:34px;line-height:34px;font-size:13px}
</style>
</head>
<body>

<header class="section hero">
  <div class="hero-photo" role="img" aria-label="Rider on an electric mountain bike above snowy New Zealand mountains"></div>
  <nav class="nav">
    <a class="nav-link" style="left:75px" href="#">Home</a>
    <a class="nav-link" style="left:168px" href="#">About Us</a>
    <a class="nav-link" style="left:291px" href="#">What We Offer</a>
    <div class="brand"><i></i>RIDGEVOLT</div>
    <a class="nav-link" style="left:764px" href="#">Bookings</a>
    <a class="nav-link" style="left:891px" href="#">Contact Us</a>
    <a class="btn nav-book" href="#">Book Now</a>
  </nav>
  <h1 class="hero-title">Electric mountain bike tours<br>in New Zealand.</h1>
  <p class="hero-sub">Donec molestie sit amet est non fermentum..</p>
  <a class="btn hero-cta" href="#">Book Your Tour</a>
  <div class="dots"><span class="on"></span><span></span><span></span><span></span></div>
  <svg class="ridge" viewBox="0 0 1200 90" preserveAspectRatio="none"><polygon fill="#fff" points="0,90 0,50 90,68 180,30 260,60 340,15 420,55 500,28 570,62 640,8 720,48 800,25 870,62 960,18 1050,55 1130,28 1200,50 1200,90"/></svg>
</header>

<section class="section about">
  <h2 class="title">About Ridgevolt</h2>
  <p class="lead">Lorem ipsum dolor sit amet, consectetur adipiscing elit. Fusce consequat erat sit amet sapien ultrices, tincidunt hendrerit velit semper. Etiam tempor condimentum neque vitae malesuada. Maecenas hendrerit ligula quis justo facilisis, quis hendrerit ante gravida. Maecenas vitae pulvinar mi. Vivamus nec pharetra elit. Nunc consectetur ex non mi maximus commodo. Nam orci nisl, condimentum in pharetra sed, dignissim vitae odio. Donec molestie sit amet est non fermentum. Morbi pellentesque et diam at faucibus.</p>
  <a class="btn" href="#">Read More</a>
</section>

<section class="section offer">
  <h2 class="title">What We Offer</h2>
  <p class="lead">Lorem ipsum dolor sit amet, consectetur adipiscing elit. Fusce consequat erat sit amet sapien ultrices, tincidunt hendrerit velit semper. Etiam tempor condimentum neque vitae malesuada.</p>
  <div class="offer-card" style="left:77px">
    <div class="photo" role="img" aria-label="Electric mountain bike parked on a hillside" style="background:linear-gradient(180deg,#7d9bc0,#5b6a4e 60%,#3d4630)"></div>
    <h3>Bike Rental</h3>
    <p>Lorem ipsum dolor sit amet, consectetur adipiscing elit. Fusce consequat erat sit amet sapien ultrices, tincidunt hendrerit velit semper. Etiam tempor condimentum neque vitae malesuada.</p>
  </div>
  <div class="offer-card" style="left:616px">
    <div class="photo" role="img" aria-label="Guide and riders on a grassy trail" style="background:linear-gradient(180deg,#8a7a3a,#6e6a2c 50%,#4f5524)"></div>
    <h3>Guided Tours</h3>
    <p>Lorem ipsum dolor sit amet, consectetur adipiscing elit. Fusce consequat erat sit amet sapien ultrices, tincidunt hendrerit velit semper. Etiam tempor condimentum neque vitae malesuada.</p>
  </div>
  <svg class="ridge" viewBox="0 0 1200 90" preserveAspectRatio="none"><polygon fill="#fff" points="0,90 0,40 100,70 190,35 270,65 360,15 440,60 520,30 600,70 690,25 770,62 850,35 930,70 1020,20 1100,60 1200,35 1200,90"/></svg>
</section>

<section class="section track">
  <h2 class="title">View Track</h2>
  <p class="lead">Lorem ipsum dolor sit amet, consectetur adipiscing elit. Fusce consequat erat sit amet sapien ultrices, tincidunt hendrerit velit semper.</p>
  <div class="fern" role="img" aria-label="Silver fern frond decoration"></div>
  <div class="video" role="img" aria-label="Video still of a rider on a mountain track">
    <svg class="play" viewBox="0 0 60 60"><circle cx="30" cy="30" r="30" fill="#fff"/><polygon points="24,18 44,30 24,42" fill="#222"/></svg>
  </div>
  <div class="kiwi" role="img" aria-label="Kiwi bird decoration"></div>
</section>

<section class="section pricing">
  <h2 class="title">Pricing Package</h2>
  <p class="lead">Lorem ipsum dolor sit amet, consectetur adipiscing elit. Fusce consequat erat sit amet sapien ultrices, tincidunt hendrerit velit semper. Etiam tempor condimentum neque vitae malesuada.</p>
  <div class="plan basic" style="left:77px">
    <div class="badge"><sup>$</sup>35.00<small>pm</small></div>
    <div class="bike" role="img" aria-label="Electric mountain bike"></div>
    <h3>Basic</h3>
    <ul><li>Duis molestie tellus</li><li>Finibus est tempus</li><li>Feugiat nibh</li><li>Laculis sagittis lectus</li></ul>
    <a class="btn" href="#">Book Now</a>
  </div>
  <div class="plan standard" style="left:436px">
    <div class="badge"><sup>$</sup>55.00<small>pm</small></div>
    <div class="bike" role="img" aria-label="Electric mountain bike"></div>
    <h3>Standard</h3>
    <ul><li>Duis molestie tellus</li><li>Finibus est tempus</li><li>Feugiat nibh</li><li>Laculis sagittis lectus</li></ul>
    <a class="btn" href="#">Book Now</a>
  </div>
  <div class="plan premium" style="left:797px">
    <div class="badge"><sup>$</sup>65.00<small>pm</small></div>
    <div class="bike" role="img" aria-label="Electric mountain bike"></div>
    <h3>Premium</h3>
    <ul><li>Duis molestie tellus</li><li>Finibus est tempus</li><li>Feugiat nibh</li><li>Laculis sagittis lectus</li></ul>
    <a class="btn" href="#">Book Now</a>
  </div>
  <svg class="ridge" viewBox="0 0 1200 90" preserveAspectRatio="none"><polygon fill="#fff" points="0,90 0,45 80,70 170,30 250,62 330,20 420,58 500,35 580,70 660,22 750,60 830,30 910,66 1000,25 1080,62 1200,40 1200,90"/></svg>
</section>

<section class="section testimonials">
  <h2 class="title">Testimonials</h2>
  <span class="arrow prev"></span>
  <div class="avatar" role="img" aria-label="Customer portrait"></div>
  <span class="arrow next"></span>
  <p class="quote">" Lorem ipsum dolor sit amet, consectetur adipiscing elit. Fusce consequat erat sit amet sapien ultrices, tincidunt hendrerit velit semper. Etiam tempor condimentum neque vitae malesuada. Maecenas hendrerit ligula quis justo facilisis, quis hendrerit ante gravida. Maecenas vitae pulvinar mi ipsum id aliquet vestibulum, metus turpis tincidunt neque ."</p>
  <p class="cite">-Name Heading</p>
</section>

<footer class="section footer">
  <div class="brand"><i></i>RIDGEVOLT</div>
  <p class="copy">Copyright © 2018 Company Name<br>All Right Reserved</p>
  <div class="social"><span></span><span></span><span></span><span></span><span></span><span></span></div>
  <div class="fcol" style="left:344px">
    <h4>Site Map</h4>
    <ul><li>Home</li><li>About us</li><li>What we offer</li><li>Bookings</li><li>Contact us</li></ul>
  </div>
  <div class="fcol" style="left:495px">
    <h4>What We Offer</h4>
    <ul><li>Lorem ipsum dolor</li><li>Sit amet</li><li>Consectetur adipiscing</li><li>Fusce consequat</li></ul>
  </div>
  <div class="fcol contact" style="left:678px;width:190px">
    <h4>Contact Us</h4>
    <ul>
      <li><svg width="12" height="14" viewBox="0 0 12 14"><path d="M6 0a5 5 0 0 1 5 5c0 4-5 9-5 9S1 9 1 5a5 5 0 0 1 5-5z" fill="#fff"/><circle cx="6" cy="5" r="2" fill="#222"/></svg><span>1510 Lorem ipsum dolor sit amet, Consectetur adipiscing</span></li>
      <li><svg width="12" height="12" viewBox="0 0 12 12"><path d="M2 0l2.5 3-1.5 1.5a7 7 0 0 0 4.5 4.5L9 7.5 12 10l-2 2C4 12 0 8 0 2z" fill="#fff"/></svg><span>1-800-555-0142</span></li>
      <li><svg width="13" height="10" viewBox="0 0 13 10"><rect width="13" height="10" fill="#fff"/><path d="M0 0l6.5 5L13 0" stroke="#222" fill="none"/></svg><span>hello@ridgevolt.example</span></li>
    </ul>
  </div>
  <div class="fcol" style="left:885px"><h4>Email Sign Up</h4></div>
  <div class="email"><svg width="14" height="11" viewBox="0 0 14 11"><rect width="14" height="11" fill="#222"/><path d="M0 0l7 5.5L14 0" stroke="#fff" fill="none"/></svg>Email Address</div>
  <a class="btn signup" href="#">Sign Up</a>
</footer>

</body>
</html>
```